Communication and Marketing agency needs a new presentation card

We are a group of communication and marketing agencies specialized in companies that are in the logistics and industrial sector. The head agency is TELVANO Grupo and the group consists of 4 agencies: TELVANO Media, TELVANO Digital, TELVANO Research and DifundeEnPantalla. We hace 4 offices in Spain (Madrid, Barcelona, Valencia and Murcia). We are looking for a clean and attractive design that transmits our experience, brand presence in the market and knowledge to those who receive the card.It has to maintain the colors of the logo that is attached.
Target Market(s)
logistics and industrial sector
Marketing department
Contact Information for Business Card
Clean and attractive design

```html
<!DOCTYPE html>
<html lang="en">
<head>
<meta charset="utf-8">
<title>TELVANO Grupo – Business Card</title>
<link rel="stylesheet" href="https://fonts.googleapis.com/css2?family=Lato:wght@400;700&family=Open+Sans:wght@600&display=swap">
<style>
  :root {
    --backdrop: #a21f22;
    --card-dark: #1c1c1c;
    --card-light: #f7f7f7;
    --ink: #2a2a2a;
    --brand-red: #b0212b;
    --brand-grey: #6a6a6a;
  }
  html, body {
    margin: 0;
    width: 1200px;
    height: 1200px;
    overflow: hidden;
    background: var(--backdrop);
  }
  .canvas {
    position: relative;
    width: 1200px;
    height: 1200px;
    font-family: "Lato", sans-serif;
  }
  .card {
    position: absolute;
    left: 224px;
    width: 814px;
    height: 466px;
    border-radius: 26px;
    box-sizing: border-box;
  }
  .card--front {
    top: 76px;
    background: var(--card-dark);
  }
  .card--back {
    top: 658px;
    background: var(--card-light);
    color: var(--ink);
  }
  .front-brand {
    position: absolute;
    right: 150px;
    top: 150px;
    text-align: right;
    color: var(--brand-grey);
    font-weight: 400;
    line-height: 1;
  }
  .front-brand__name {
    display: block;
    font-size: 96px;
    letter-spacing: 6px;
  }
  .front-brand__unit {
    display: block;
    font-size: 58px;
    margin-top: 10px;
  }
  .holder {
    position: absolute;
    left: 94px;
    top: 100px;
  }
  .holder__name {
    font-family: "Open Sans", sans-serif;
    font-weight: 600;
    font-size: 38px;
    letter-spacing: -1.5px;
    line-height: 1;
    margin: 0;
  }
  .holder__role {
    color: var(--brand-red);
    font-size: 20px;
    letter-spacing: -0.5px;
    margin-top: 6px;
  }
  .contact {
    position: absolute;
    left: 510px;
    font-size: 20px;
    line-height: 25px;
  }
  .contact--direct { top: 106px; }
  .contact--address { top: 262px; }
  .contact__label { color: var(--brand-red); }
  .contact__web {
    color: var(--brand-red);
    margin-top: 16px;
    letter-spacing: 1px;
  }
  .back-brand {
    position: absolute;
    left: 90px;
    top: 280px;
    text-align: right;
    color: var(--brand-red);
    font-weight: 700;
    line-height: 1;
  }
  .back-brand__name {
    display: block;
    font-size: 50px;
    letter-spacing: 2px;
  }
  .back-brand__unit {
    display: block;
    font-size: 32px;
    margin-top: 8px;
  }
</style>
</head>
<body>
<main class="canvas">
  <section class="card card--front" aria-label="Card front">
    <div class="front-brand">
      <span class="front-brand__name">TELVANO</span>
      <span class="front-brand__unit">Digital</span>
    </div>
  </section>

  <section class="card card--back" aria-label="Card back">
    <div class="holder">
      <h1 class="holder__name">MARISOL VEGA</h1>
      <div class="holder__role">Executive Assistant</div>
    </div>

    <div class="contact contact--direct">
      <div><span class="contact__label">P.</span> +281 - 555 - 0137</div>
      <div>marisol@mail.com</div>
    </div>

    <div class="back-brand">
      <span class="back-brand__name">TELVANO</span>
      <span class="back-brand__unit">Grupo</span>
    </div>

    <div class="contact contact--address">
      <div>Harlow PKWY Ste.</div>
      <div>A Brenton, TX 77500</div>
      <div>Mill Street. LEEDS</div>
      <div class="contact__web">www.telvano.org</div>
    </div>
  </section>
</main>
</body>
</html>
```